WE ARE BRIGHT SPARROW, building a full website with ecommerce

requirements:
CODED FOR SITEQUILL
ONLINE STORE FUNCTION WITH E-COMMERCE USING TRADEBLOOM
PAGEWAVE AND PICTOLANE LINKS

I need a website design for my organization, WE ARE BRIGHT SPARROW, a global empowerment movement elevating woman, and the world. The site's home page should reflect our mission, to empower women. It should have a strong, empowering feel, with minimalistic design.
Please see www.lunavelto.com and http://www.corvenhal.co/ for an inspiration on layout and feel.

**PLEASE SEE ATTACHMENT "LOGO MOCK UP" FOR LOGO. THIS IS NOT THE FINAL VECTOR FILE, BUT THIS LOOKS THE SAME AS THE FINAL LOGO.

HOME PAGE:
The first section of the home page should include a background image with our logo center.

You should include the following links to pages at the top right of the page:
MISSION
MANTRA
ARMOR
MEET BS (I would like "bs" to be our logo)
pagewave and pictolane links

As you scroll down the page, you should see the following sections, which correlate to the links to pages as written above. **SEE ATTACHED SKETCH "HOMEPAGE LAYOUT IDEA" FOR REFERENCE**

WHO WE ARE (correlates to the link Mission)

OUR MANTRA (correlates to the link Mantra)

OUR ARMOR (correlates to the link The Shirt)
(This is where we will sell a shirt (and other apparel) and need the e-commerce function)

MEET BRIGHT SPARROWS (correlates to the link Meet BS)

SHOW OFF YOUR SUPER POWERS (correlates to the pagewave and pictolane)

FEATURED BRIGHT SPARROW (no link on top right of page)

On the homepage, for each of the above sections, as you scroll down there should be an image, either in the background or framed, next to the title (WHO WE ARE, for example), as well as one sentence of small text explaining the title. The title (WHO WE ARE) and the one sentence should link to a page (ie WHO WE ARE + the one sentence links to the MISSION page). ** SEE ATTACHED SKETCH "HOMEPAGE SECTION IDEAS" FOR REFERENCE**

**PLEASE SEE ATTACHMENT "WEBSITE TITLE IDEAS" FOR A STARTING PLACE OF THE LOOK. These don't have to be exact, but they give you an idea of what I'm looking for.

**FONTS TYPOLD EXTRA BOLD AND TYPOLD BOOK 500 (WHICH SHOULD BE BOLDED MANUALLY) ARE ATTACHED**

Target Market(s)

Women, mainly in US

Industry/Entity Type

Social

Coding

Coded - Design and coding required

Number of Pages Required

5+ page

Font styles to use
Other font styles liked:
• Typol Extra Bold

Requirements
Must have
• CODED FOR SITEQUILL
• ONLINE STORE FUNCTION WITH E-COMMERCE USING TRADEBLOOM
• PAGEWAVE AND PICTOLANE LINKS
• Typold Extra Bold and Typold Book 500, attached
• please see description for all requirements
Nice to have
• please see description for all ideas
Should not have

```html
<!DOCTYPE html>
<html lang="en">
<head>
<meta charset="utf-8">
<title>We Are Bright Sparrow</title>
<link rel="stylesheet" href="https://fonts.googleapis.com/css2?family=Montserrat:wght@400;500;600;700;800&display=swap">
<style>
:root{
  --ink:#111111;
  --text:#2a2a2a;
  --muted:#6b6b6b;
  --paper:#ffffff;
  --mist:#e9e9e9;
  --fog:#f1f2f3;
  --line:#d7d7d7;
  --night:#0e0e0e;
  --stone-dark:#3a3a3a;
  --stone-light:#8a8a8a;
}
*{box-sizing:border-box;margin:0;padding:0}
html,body{width:1200px;height:4296px;overflow:hidden}
body{font-family:"Montserrat",Arial,sans-serif;color:var(--text);background:var(--paper);position:relative}
section,header,footer{position:relative;width:1200px;overflow:hidden}
.photo{position:absolute}
.mark{display:inline-block;border:5px solid var(--ink);flex:none}
.brand{display:flex;align-items:center;gap:16px;color:var(--ink);font-weight:800;text-transform:uppercase;line-height:1}

/* header / hero */
.hero{height:596px;background:linear-gradient(90deg,#eef0f1 0%,#f7f7f7 45%,#ffffff 100%)}
.hero .photo{left:110px;top:60px;width:460px;height:536px;background:linear-gradient(180deg,#e3d6c6 0%,#cfc8c2 45%,#bfc3c8 100%);border-radius:4px}
.site-logo{position:absolute;left:100px;top:22px}
.site-logo .mark{width:52px;height:52px}
.site-logo span{font-size:19px;width:170px;line-height:1.05}
.main-nav{position:absolute;right:120px;top:36px;display:flex;gap:34px;font-size:15px;font-weight:500;letter-spacing:.5px;color:var(--ink)}
.side-links{position:absolute;right:0;top:88px;display:flex;flex-direction:column;gap:8px}
.side-links span{width:44px;height:44px;border-radius:50%;background:var(--stone-dark)}
.arrow{position:absolute;top:270px}
.hero-center{position:absolute;left:0;right:0;top:168px;display:flex;flex-direction:column;align-items:center;text-align:center}
.hero-center .mark{width:120px;height:120px;border-width:12px}
.hero-center h1{margin-top:26px;font-size:34px;font-weight:800;color:var(--ink);letter-spacing:.5px}
.hero-center p{margin-top:8px;font-size:19px;font-weight:500;color:var(--ink);letter-spacing:.5px}
.signup{margin-top:22px;display:flex;gap:14px;margin-left:220px}
.signup .field{width:340px;height:34px;border-bottom:1px solid var(--line);background:rgba(255,255,255,.9);font-size:14px;text-align:left;padding:8px 10px;color:var(--text)}
.btn{display:inline-block;background:var(--ink);color:#fff;border-radius:20px;font-weight:700;font-size:14px;padding:9px 26px;letter-spacing:.5px}

/* statement */
.statement{height:192px;text-align:center;padding-top:26px}
.statement p{font-size:24px;font-weight:500;color:var(--ink);line-height:1.35;letter-spacing:.5px}
.statement .brand{justify-content:center;margin-top:20px;font-size:22px}
.statement .mark{width:34px;height:34px;border-width:4px}

/* feature sections */
.feature .copy{position:absolute;z-index:1}
.feature h2{display:flex;align-items:center;gap:22px;font-size:34px;font-weight:800;color:var(--ink);line-height:1.0;text-transform:uppercase}
.feature h2 .mark{width:88px;height:88px;border-width:9px}
.feature p{margin-top:30px;font-size:14px;line-height:2.0;color:var(--text);text-align:justify}
.who{height:492px;background:var(--mist)}
.who .photo{left:587px;top:0;width:530px;height:492px;background:linear-gradient(180deg,#3a2b24 0%,#7a5a49 35%,#f2f0ee 75%,#ffffff 100%)}
.who .copy{left:118px;top:148px;width:435px}
.mantra{height:516px;background:linear-gradient(90deg,#e4e7ea 0%,#f1f3f5 60%,#eef0f2 100%)}
.mantra .photo{left:0;top:0;width:620px;height:516px;background:linear-gradient(160deg,#d9dde1 0%,#f5f5f5 40%,#e6e2de 70%,#cfd3d8 100%)}
.mantra .copy{left:692px;top:125px;width:440px}
.mantra h2{font-size:26px}
.meet{height:561px;background:linear-gradient(90deg,#ffffff 0%,#f7f7f7 55%,#e9ecef 100%)}
.meet .photo{left:560px;top:50px;width:640px;height:511px;background:linear-gradient(180deg,#7a5a40 0%,#c9a083 35%,#efe9e3 70%,#dfe3e6 100%)}
.meet .copy{left:100px;top:160px;width:430px}
.meet h2{font-size:26px}
.meet h2 .mark{width:96px;height:96px}

/* armor */
.armor{height:788px;background:var(--paper)}
.section-title{display:flex;justify-content:center;align-items:center;gap:18px}
.section-title .mark{width:96px;height:96px;border-width:10px}
.section-title h2{font-size:26px;font-weight:800;color:var(--ink);line-height:1.05;text-transform:uppercase}
.armor .section-title{padding-top:58px}
.products{display:flex;justify-content:center;gap:55px;margin-top:58px}
.product{width:290px;text-align:center}
.product .frame{height:355px;border:1px solid var(--line);padding:22px;background:var(--paper);box-shadow:0 2px 10px rgba(0,0,0,.06)}
.product .photo{position:static;width:100%;height:100%}
.product h3{margin-top:34px;font-size:15px;font-weight:500;color:var(--ink)}
.product .price{margin-top:12px;font-size:40px;font-weight:500;color:var(--ink)}
.product .btn{margin-top:14px;padding:10px 38px;font-weight:600}

/* superpowers */
.powers{height:349px;background:linear-gradient(180deg,#5a5a5a 0%,#9a9a9a 40%,#3c3c3c 75%,#1c1c1c 100%)}
.powers .inner{position:absolute;left:275px;top:110px;display:flex;align-items:center;gap:24px}
.powers .mark{width:96px;height:96px;border-color:#fff;border-width:10px}
.powers h2{color:#fff;font-weight:800;font-size:30px;line-height:1.05}
.powers h2 small{display:block;font-size:14px;font-weight:700;margin-bottom:4px}
.socials{position:absolute;left:670px;top:128px;display:flex;gap:42px}
.social{display:flex;align-items:center;gap:10px;color:#fff;font-size:14px;font-weight:700}
.social span.dot{width:60px;height:60px;border:2px solid #fff;border-radius:50%}

/* featured */
.featured{height:510px;background:var(--paper)}
.featured .section-title{padding-top:60px}
.portraits{position:absolute;top:270px;left:0;right:0;display:flex;justify-content:center;gap:105px}
.diamond{width:148px;height:148px;transform:rotate(45deg);box-shadow:8px 8px 18px rgba(0,0,0,.25);position:relative}
.diamond.a{background:linear-gradient(135deg,#c9a48c,#e8d9cd)}
.diamond.c{background:linear-gradient(135deg,#d6c7bb,#9c7d68)}
.diamond.d{background:linear-gradient(135deg,#efe8e2,#b99a86)}
.diamond.active{background:var(--ink);width:156px;height:156px}
.diamond .label{position:absolute;inset:0;transform:rotate(-45deg);display:flex;flex-direction:column;align-items:center;justify-content:center;color:#fff;font-weight:800;font-size:22px;letter-spacing:1px}

/* footer */
.site-footer{height:292px;background:var(--night);color:#fff;text-align:center}
.site-footer .brand{color:#fff;justify-content:center;padding-top:52px;font-size:22px}
.site-footer .mark{width:64px;height:64px;border-color:#fff;border-width:7px}
.site-footer .brand span{text-align:left;width:130px;line-height:1.05}
.footer-nav{display:flex;justify-content:center;gap:34px;margin-top:38px;font-size:15px;font-weight:500}
.footer-social{margin-top:26px;display:flex;justify-content:center;gap:16px;font-size:11px;font-weight:600}
.copyright{margin-top:16px;font-size:11px}
</style>
</head>
<body>

<header class="hero">
  <div class="photo" role="img" aria-label="Hero photograph of a smiling woman at her desk"></div>
  <div class="site-logo brand"><i class="mark"></i><span>We Are Bright Sparrow</span></div>
  <nav class="main-nav"><span>MISSION</span><span>MANTRA</span><span>MEET BS</span><span>ARMOR</span></nav>
  <div class="side-links" aria-label="Pagewave and Pictolane links"><span></span><span></span></div>
  <svg class="arrow" style="left:100px" width="20" height="40" viewBox="0 0 20 40"><path d="M18 2 2 20l16 18" fill="none" stroke="#888" stroke-width="2"/></svg>
  <svg class="arrow" style="right:100px" width="20" height="40" viewBox="0 0 20 40"><path d="M2 2l16 18L2 38" fill="none" stroke="#888" stroke-width="2"/></svg>
  <div class="hero-center">
    <i class="mark"></i>
    <h1>WE ARE BRIGHT SPARROW</h1>
    <p>AND I WILL CONQUER THE WORLD</p>
    <div class="signup"><span class="field">Bright sparrows@email.com</span><span class="btn">LETS FLY</span></div>
  </div>
</header>

<section class="statement">
  <p>WE ARE BRIGHT SPARROW IS A GLOBAL EMPOWERMENT MOVEMENT<br>ELEVATING WOMEN... AND THE WORLD.</p>
  <div class="brand"><i class="mark"></i><span>LET'S FLY</span></div>
</section>

<section class="feature who">
  <div class="photo" role="img" aria-label="Portrait of a smiling woman with curly hair and glasses"></div>
  <div class="copy">
    <h2><i class="mark"></i><span>Who<br>We<br>Are</span></h2>
    <p>Sed ut perspiciatis unde omnis iste natus error sit voluptatem accusantium doloremque laudantium, totam rem aperiam, eaque ipsa quae ab illo inventore veritatis et quasi architecto beatae vitae dicta sunt explicabo.</p>
  </div>
</section>

<section class="feature mantra">
  <div class="photo" role="img" aria-label="Woman meditating in a bright office"></div>
  <div class="copy">
    <h2><i class="mark"></i><span>Our<br>Mantra</span></h2>
    <p>Sed ut perspiciatis unde omnis iste natus error sit voluptatem accusantium doloremque laudantium, totam rem aperiam, eaque ipsa quae ab illo inventore veritatis et quasi architecto beatae vitae dicta sunt explicabo.</p>
  </div>
</section>

<section class="feature meet">
  <div class="photo" role="img" aria-label="Smiling woman with curly hair in a white blouse"></div>
  <div class="copy">
    <h2><i class="mark"></i><span>Meet<br>Bright<br>Sparrow</span></h2>
    <p>Sed ut perspiciatis unde omnis iste natus error sit voluptatem accusantium doloremque laudantium, totam rem aperiam, eaque ipsa quae ab illo inventore veritatis et quasi architecto beatae vitae dicta sunt explicabo.</p>
  </div>
</section>

<section class="armor">
  <div class="section-title"><i class="mark"></i><h2>Our<br>Armor</h2></div>
  <div class="products">
    <div class="product">
      <div class="frame"><div class="photo" role="img" aria-label="Woman wearing a black logo t-shirt" style="background:linear-gradient(180deg,#f2f2f2 0%,#c9a58c 35%,#1c1c1c 60%,#2a2a2a 100%)"></div></div>
      <h3>FINIBUS BONORUM ET MALORUM</h3><div class="price">$50.90</div><span class="btn">BUY NOW</span>
    </div>
    <div class="product">
      <div class="frame" style="box-shadow:0 4px 22px rgba(0,0,0,.14)"><div class="photo" role="img" aria-label="Woman wearing a white logo t-shirt" style="background:linear-gradient(180deg,#f2f2f2 0%,#3a2b24 25%,#e9e9e9 55%,#3a4a5a 100%)"></div></div>
      <h3>FINIBUS BONORUM ET MALORUM</h3><div class="price">$50.90</div><span class="btn">BUY NOW</span>
    </div>
    <div class="product">
      <div class="frame"><div class="photo" role="img" aria-label="Woman wearing a red logo t-shirt" style="background:linear-gradient(180deg,#f2f2f2 0%,#d9b48a 30%,#c8202a 55%,#3a4a6a 100%)"></div></div>
      <h3>FINIBUS BONORUM ET MALORUM</h3><div class="price">$50.90</div><span class="btn">BUY NOW</span>
    </div>
  </div>
</section>

<section class="powers" role="img" aria-label="Misty mountain landscape with a figure on a peak">
  <div class="inner"><i class="mark"></i><h2><small>SHOW OFF YOUR</small>SUPER<br>POWERS</h2></div>
  <div class="socials">
    <div class="social"><span class="dot"></span>PAGEWAVE</div>
    <div class="social"><span class="dot"></span>PICTOLANE</div>
  </div>
</section>

<section class="featured">
  <div class="section-title"><i class="mark"></i><h2>Featured<br>Bright<br>Sparrow</h2></div>
  <div class="portraits">
    <div class="diamond a" role="img" aria-label="Featured member portrait"></div>
    <div class="diamond active"><div class="label">MARELA<svg width="14" height="10" viewBox="0 0 14 10" style="margin-top:8px"><path d="M0 0h14L7 10z" fill="#fff"/></svg></div></div>
    <div class="diamond c" role="img" aria-label="Featured member portrait"></div>
    <div class="diamond d" role="img" aria-label="Featured member portrait"></div>
  </div>
</section>

<footer class="site-footer">
  <div class="brand"><i class="mark"></i><span>We Are Bright Sparrow</span></div>
  <nav class="footer-nav"><span>MISSION</span><span>MANTRA</span><span>MEET BS</span><span>ARMOR</span></nav>
  <div class="footer-social"><span>PAGEWAVE</span><span>PICTOLANE</span></div>
  <p class="copyright">© 2017 www.companyname.com</p>
</footer>

</body>
</html>
```